VORNAK SYSTEMS BUSINESS CARD DESIGN

WE WANT COMPLETE NEW DESIGN OF OUR BUSINESS CARD. WE ARE AN INTEGRATION COMPANY, WHERE WE INTEGRATE IOT/SMART SYSTEMS TO HOMES AND CORPORATE CUSTOMERS. WE SUPPLY AND INSTALL AUTOMATION PRODUCTS. THE FINAL DESIGN SHOULD COMMUNICATE TECHNOLOGY. THE CARD DESIGN SHOULD BE VERY IMPACT FULL. LOGO NEEDS TO BE THERE. IT WOULD NICE IF THE DESIGN WAS CLEAN. COLORS IS UP TO DESIGNER TO PLAY WITH, OR CAN STICK TO CORPORATE COLORS (FOLLOW LOGO). I HAVE ADDED FEW REFERENCE PHOTOS TO DRAW INSPIRATION MAYBE. I HAVE ADDED A HEX DESIGN, ITS NOT NECESSARY TO USE THIS DESIGN, ITS UPTO DESIGNER, JUST ADDED IF NEEDED TO PLAY WITH DESIGN.

Target Market(s)

Private end users and corporate clients

Industry/Entity Type

technology, home automation, home theaters, building management systems, IOT

Contact Information for Business Card

It should include Employee name, personal number, office number, email address, both in English and arabic. DETAILS TO INCLUDE :RAJESH PALLIVAL, MOBILE 0097150738265,OFFCIE 009714368547, RAJESH@VORNAKSYS.EXAMPLE

Requirements
Must have
• Should feel like a technology company from design. Details both and in English and arabic (or at least have provision for arabic in design).
Nice to have
• I would like logo on one side, and details on the other side. Logo design side should communicate technology with logo. Other side can be clean just with information or also have some design aspects following from logo side. it would be interesting to see submissions with square design as well (that looks like an app Icon). colors could be of logo, red black grey and white. I have added some designs to draw inspiration from

```html
<!DOCTYPE html>
<html lang="en">
<head>
<meta charset="utf-8">
<title>Vornak Systems – Business Card</title>
<link rel="stylesheet" href="https://fonts.googleapis.com/css2?family=Noto+Kufi+Arabic:wght@400;700&family=Open+Sans:wght@400;600;700&display=swap">
<style>
  :root {
    --backdrop: #1b1b1b;
    --card: #2a2a2b;
    --card-edge: #232324;
    --ink-white: #f2f2f2;
    --ink-grey: #a9a9ab;
    --ink-dim: #6a6a6d;
    --accent-red: #e3141b;
    --trace-glow: rgba(160,160,166,0.16);
  }
  * { box-sizing: border-box; margin: 0; padding: 0; }
  html, body { width: 1200px; height: 800px; overflow: hidden; background: var(--backdrop); }
  body { font-family: "Open Sans", Arial, sans-serif; position: relative; }

  .card {
    position: absolute;
    left: 320px;
    width: 560px;
    height: 320px;
    background: var(--card);
    border: 1px solid var(--card-edge);
    overflow: hidden;
  }
  .card--front { top: 60px; }
  .card--back { top: 420px; }

  .circuit-field {
    position: absolute;
    background: radial-gradient(ellipse at 50% 50%, var(--trace-glow) 0%, rgba(160,160,166,0.06) 45%, transparent 72%);
  }
  .card--front .circuit-field { left: -20px; top: 10px; width: 300px; height: 310px; }
  .card--back .circuit-field { right: -20px; top: -10px; width: 320px; height: 250px; }

  .brand { position: absolute; white-space: nowrap; }
  .card--front .brand { left: 270px; top: 118px; }
  .card--back .brand { left: 36px; top: 34px; }

  .brand__name {
    display: flex;
    align-items: center;
    gap: 10px;
    font-weight: 700;
    font-size: 27px;
    letter-spacing: 1px;
    line-height: 1;
  }
  .card--front .brand__name { color: var(--ink-grey); }
  .card--back .brand__name { color: var(--ink-white); font-size: 23px; }
  .brand__mark { width: 20px; height: 20px; background: var(--accent-red); flex: none; }
  .card--front .brand__mark { background: var(--ink-grey); }

  .brand__tagline {
    margin-top: 10px;
    font-size: 10px;
    letter-spacing: 3.6px;
    text-transform: uppercase;
  }
  .card--front .brand__tagline { color: var(--ink-dim); }
  .card--back .brand__tagline { color: var(--ink-white); font-size: 9px; letter-spacing: 3px; }

  .contact { position: absolute; left: 36px; top: 124px; color: var(--ink-white); }
  .contact__name { color: var(--accent-red); font-weight: 700; font-size: 16px; line-height: 1.3; letter-spacing: 0.3px; }
  .contact__role { font-size: 12px; line-height: 1.4; margin-bottom: 8px; }
  .contact__address { font-size: 12px; line-height: 1.4; margin-bottom: 8px; }
  .contact__list { list-style: none; font-size: 12px; line-height: 1.45; }
  .contact__list li { display: flex; align-items: center; gap: 8px; }
  .contact__icon { width: 11px; height: 11px; fill: var(--accent-red); flex: none; }

  .contact-ar {
    position: absolute;
    right: 30px;
    bottom: 26px;
    direction: rtl;
    text-align: right;
    font-family: "Noto Kufi Arabic", "Open Sans", sans-serif;
    color: var(--ink-white);
  }
  .contact-ar__name { color: var(--accent-red); font-weight: 700; font-size: 15px; line-height: 1.5; }
  .contact-ar__role { font-size: 11px; line-height: 1.6; }
  .contact-ar__address { font-size: 11px; line-height: 1.6; }
</style>
</head>
<body>

<section class="card card--front" aria-label="Card front">
  <div class="circuit-field" role="img" aria-label="Decorative circuit-board trace pattern in soft grey"></div>
  <div class="brand">
    <div class="brand__name"><span class="brand__mark"></span>VORNAK SYSTEMS</div>
    <div class="brand__tagline">A Vornak Group Division</div>
  </div>
</section>

<section class="card card--back" aria-label="Card back">
  <div class="circuit-field" role="img" aria-label="Decorative circuit-board trace pattern in soft grey"></div>
  <div class="brand">
    <div class="brand__name"><span class="brand__mark"></span>VORNAK SYSTEMS</div>
    <div class="brand__tagline">A Vornak Group Division</div>
  </div>

  <div class="contact">
    <div class="contact__name">RAJESH PALLIVAL</div>
    <div class="contact__role">President</div>
    <div class="contact__address">18 Cedar Court<br>Al Qusais, Dubai 48213</div>
    <ul class="contact__list">
      <li>
        <svg class="contact__icon" viewBox="0 0 12 12" aria-hidden="true"><path d="M2.5 1l2 2.2-1 1.3c.8 1.6 2 2.8 3.6 3.6l1.3-1 2.2 2-1.2 1.7C5 10.5 1.5 7 .8 2.2z"/></svg>
        0097150738265
      </li>
      <li>
        <svg class="contact__icon" viewBox="0 0 12 12" aria-hidden="true"><path d="M3 0h6v12H3zM4 1.5v8h4v-8z" fill-rule="evenodd"/></svg>
        009714368547
      </li>
      <li>
        <svg class="contact__icon" viewBox="0 0 12 12" aria-hidden="true"><path d="M0 2h12v8H0zM1 3l5 3.5L11 3z" fill-rule="evenodd"/></svg>
        rajesh@vornaksys.example
      </li>
      <li>
        <svg class="contact__icon" viewBox="0 0 12 12" aria-hidden="true"><circle cx="6" cy="6" r="5.5"/><path d="M.5 6h11M6 .5c2 2 2 9 0 11M6 .5c-2 2-2 9 0 11" stroke="#2a2a2b" stroke-width="0.9" fill="none"/></svg>
        www.vornaksys.example
      </li>
    </ul>
  </div>

  <div class="contact-ar" lang="ar">
    <div class="contact-ar__name">راجش باليفال</div>
    <div class="contact-ar__role">الرئيس</div>
    <div class="contact-ar__address">١٨ سيدار كورت، القصيص، دبي</div>
  </div>
</section>

</body>
</html>
```